Tidewell Comforts, a portable luxury restroom trailer company needs a landing page

We need a landing page for a luxury portable restroom trailer company. This should be modern, and simple - use any combination of Pantone colors: Warm Gray 1C, Black 7C, 7529c, 873C, 8003C

We rent these trailers for special events like weddings, private parties, festivals, family reunions, team building, wine tastings, beer tastings, food truck round-ups, etc.

An idea of the landing page is in the files below. Please use stock photography and placeholder text for now. The winning design will be given final content.

Requirements
Must have
• Multiple "Get Quote" buttons or a place for them to type in type of rental, how many people etc

```html
<!DOCTYPE html>
<html lang="en">
<head>
<meta charset="utf-8">
<title>Tidewell Comforts — Luxury Restroom Trailers</title>
<link rel="stylesheet" href="https://fonts.googleapis.com/css2?family=Saira:wght@500;600;700&family=Roboto:wght@400;500;700&display=swap">
<style>
:root{
  --gold:#bfa274;
  --gold-dark:#a98a5c;
  --ink:#241008;
  --text:#1c1c1c;
  --muted:#5b5b5b;
  --paper:#ffffff;
  --mist:#f0f1f3;
  --line:#dcdcdc;
}
*{box-sizing:border-box;margin:0;padding:0}
html,body{width:1200px;height:3183px;overflow:hidden;background:var(--paper);font-family:"Roboto",sans-serif;color:var(--text)}
.page{position:relative;width:1200px;height:3183px}
.abs{position:absolute}

/* header */
.site-header{position:absolute;left:0;top:0;width:1200px;height:75px;background:var(--paper)}
.brand{position:absolute;left:111px;top:24px;font-family:"Saira",sans-serif;font-weight:600;font-size:25px;letter-spacing:.5px;color:var(--gold-dark);text-transform:uppercase}
.nav{position:absolute;left:598px;top:32px;display:flex;gap:33px;font-size:13.5px;font-weight:500;text-transform:uppercase}
.nav a{color:var(--text);text-decoration:none}
.nav a.active{color:var(--gold)}
.btn-login{position:absolute;left:975px;top:19px;width:114px;height:42px;border-radius:21px;background:var(--ink);color:#fff;font-size:13.5px;font-weight:700;display:flex;align-items:center;justify-content:center;gap:8px}

/* hero */
.hero{position:absolute;left:0;top:75px;width:1200px;height:450px;background:var(--mist)}
.hero h1{position:absolute;left:111px;top:80px;font-family:"Saira",sans-serif;font-weight:700;font-size:32px;line-height:47px;letter-spacing:1px;text-transform:uppercase;color:var(--text)}
.hero p{position:absolute;left:112px;top:235px;width:460px;font-size:15.5px;line-height:26px;color:var(--muted)}
.btn-start{position:absolute;left:111px;top:314px;width:174px;height:44px;border-radius:22px;background:var(--ink);color:#fff;font-size:13.5px;font-weight:700;display:flex;align-items:center;justify-content:center;gap:10px}
.hero-grid{position:absolute;left:600px;top:0;width:600px;height:450px}
.tile{position:absolute}

/* section titles */
.section-title{position:absolute;left:0;width:1200px;text-align:center;font-family:"Saira",sans-serif;font-weight:600;font-size:28px;letter-spacing:1px;text-transform:uppercase;color:var(--text)}

/* events */
.event-card{position:absolute;width:315px;height:308px;background:var(--paper);border-radius:12px;box-shadow:0 0 0 2px #ececec,0 3px 10px rgba(0,0,0,.08);overflow:hidden}
.event-card .photo{position:absolute;left:4px;top:4px;width:307px;height:235px;border-radius:8px 8px 0 0}
.event-card h3{position:absolute;left:0;top:260px;width:100%;text-align:center;font-size:21px;font-weight:700}
.event-card.is-active{background:var(--gold);box-shadow:0 6px 14px rgba(0,0,0,.18)}
.event-card.is-active h3{color:#fff}

/* products */
.products{position:absolute;left:0;top:1432px;width:1200px;height:731px;background:var(--mist)}
.product-card{position:absolute;width:477px;height:238px;background:var(--paper);box-shadow:0 2px 8px rgba(0,0,0,.06)}
.product-card .photo{position:absolute;left:25px;top:35px;width:155px;height:170px;border-radius:14px 14px 4px 4px}
.product-card h3{position:absolute;left:216px;top:45px;font-size:20px;font-weight:700}
.product-card .rule{position:absolute;left:216px;top:76px;width:32px;height:3px;background:var(--text)}
.product-card p{position:absolute;left:216px;top:94px;width:238px;font-size:14.5px;line-height:22px;color:var(--muted);text-align:justify}
.product-card .more{position:absolute;left:216px;top:180px;font-size:12.5px;font-weight:700;text-decoration:underline;color:var(--text)}
.product-card.is-dark{background:var(--ink)}
.product-card.is-dark h3,.product-card.is-dark p,.product-card.is-dark .more{color:#fff}
.product-card.is-dark .rule{background:#fff}

/* contact */
.contact{position:absolute;left:0;top:2163px;width:1200px;height:532px;background:linear-gradient(180deg,#c6aa7a,#bb9d6c)}
.contact-band{position:absolute;left:0;top:2695px;width:1200px;height:435px;background:var(--ink)}
.contact h2{position:absolute;left:0;top:68px;width:1200px;text-align:center;font-family:"Saira",sans-serif;font-weight:600;font-size:28px;color:#fff;text-transform:uppercase;letter-spacing:.5px}
.contact p{position:absolute;left:110px;top:113px;width:980px;text-align:center;font-size:14.5px;line-height:24px;color:#fff}
.quote{position:absolute;left:195px;top:2355px;width:811px;height:479px;background:var(--paper);border-left:8px solid #3a3a3a;border-right:8px solid #3a3a3a}
.quote h3{position:absolute;left:0;top:55px;width:100%;text-align:center;font-family:"Saira",sans-serif;font-weight:600;font-size:27px;text-transform:uppercase;letter-spacing:.5px}
.field{position:absolute;width:332px;height:49px;border:1px solid var(--line);font-size:13.5px;color:#555;padding:0 20px;display:flex;align-items:center;justify-content:space-between}
.field svg{width:13px;height:13px;fill:#555}
.btn-submit{position:absolute;left:67px;top:383px;width:673px;height:47px;background:var(--ink);color:#fff;font-size:13.5px;font-weight:700;display:flex;align-items:center;justify-content:center;text-transform:uppercase}

/* footer */
.footer h4{position:absolute;font-size:13px;font-weight:700;color:#fff;text-transform:uppercase}
.footer .about{position:absolute;left:112px;top:2928px;width:290px;font-size:14px;line-height:25px;color:#e8e2da}
.footer ul{position:absolute;list-style:none}
.footer li{height:31px;font-size:14px;color:#e8e2da;display:flex;align-items:flex-start;gap:16px}
.footer li::before{content:"»";color:#fff;font-size:14px}
.social{position:absolute;left:112px;top:3055px;display:flex;gap:12px}
.social span{width:34px;height:34px;border:1.5px solid #fff;border-radius:50%;display:block}
.bottom-bar{position:absolute;left:0;top:3130px;width:1200px;height:53px;background:var(--gold);display:flex;align-items:center;justify-content:center;color:#fff;font-size:14px}
</style>
</head>
<body>
<div class="page">

  <header class="site-header">
    <div class="brand">Tidewell Comforts</div>
    <nav class="nav">
      <a class="active" href="#">Home</a><a href="#">Events</a><a href="#">Products</a><a href="#">Contact</a>
    </nav>
    <div class="btn-login">LOG IN
      <svg width="10" height="12" viewBox="0 0 10 12"><rect x="0" y="5" width="10" height="7" rx="1" fill="#fff"/><path d="M2.5 5V3.5a2.5 2.5 0 0 1 5 0V5" stroke="#fff" stroke-width="1.6" fill="none"/></svg>
    </div>
  </header>

  <section class="hero">
    <h1>We rent these portable<br>restroom trailers for<br>special events</h1>
    <p>Lorem ipsum dolor sit amet, consectetur adipiscing elit, sed do eiusmod tempor incididunt ut labore et dolore</p>
    <div class="btn-start">GET STARTED
      <svg width="14" height="14" viewBox="0 0 14 14"><circle cx="7" cy="7" r="7" fill="#fff"/><path d="M5.5 4l3 3-3 3" stroke="#241008" stroke-width="2" fill="none"/></svg>
    </div>
    <div class="hero-grid">
      <div class="tile" style="left:0;top:0;width:180px;height:148px;background:linear-gradient(135deg,#2fb3a8,#9aa7a8)" role="img" aria-label="Workers beside a row of teal portable toilets"></div>
      <div class="tile" style="left:183px;top:0;width:234px;height:148px;background:linear-gradient(135deg,#e86a2a,#5f7a4a)" role="img" aria-label="Orange portable toilets on grass"></div>
      <div class="tile" style="left:420px;top:0;width:180px;height:148px;background:linear-gradient(135deg,#5f6b76,#8fa3ae)" role="img" aria-label="Grey portable toilets"></div>
      <div class="tile" style="left:0;top:151px;width:234px;height:148px;background:linear-gradient(90deg,#2a63c6,#e0407a)" role="img" aria-label="Blue and pink portable toilets"></div>
      <div class="tile" style="left:237px;top:151px;width:180px;height:148px;background:linear-gradient(180deg,#8aa3c4,#6e7a5a)" role="img" aria-label="Portable toilets in a hillside field"></div>
      <div class="tile" style="left:420px;top:151px;width:180px;height:148px;background:linear-gradient(135deg,#33a9d8,#6a9a4a)" role="img" aria-label="Blue portable toilets at an outdoor event"></div>
      <div class="tile" style="left:0;top:302px;width:180px;height:148px;background:linear-gradient(135deg,#bfc2c0,#7b7f7c)" role="img" aria-label="Silver restroom trailer with steps"></div>
      <div class="tile" style="left:183px;top:302px;width:180px;height:148px;background:linear-gradient(135deg,#9a5b30,#d23a3a)" role="img" aria-label="Red portable toilets between wooden walls"></div>
      <div class="tile" style="left:366px;top:302px;width:234px;height:148px;background:linear-gradient(135deg,#d8d4cc,#9c3a34)" role="img" aria-label="White restroom trailer with red signs"></div>
    </div>
  </section>

  <h2 class="section-title" style="top:607px">Events</h2>

  <div class="event-card" style="left:107px;top:680px"><div class="photo" style="background:linear-gradient(160deg,#4b6a3a,#2b3542)" role="img" aria-label="Dark slatted restroom cabin in a forest"></div><h3>Weddings</h3></div>
  <div class="event-card" style="left:443px;top:680px"><div class="photo" style="background:linear-gradient(160deg,#e9e6df,#2f5fb3)" role="img" aria-label="Portable toilets on a city street"></div><h3>Private Parties</h3></div>
  <div class="event-card" style="left:779px;top:680px"><div class="photo" style="background:linear-gradient(160deg,#e9e9e4,#5a5a52)" role="img" aria-label="White restroom trailer with open doors"></div><h3>Festivals</h3></div>
  <div class="event-card" style="left:107px;top:1024px"><div class="photo" style="background:linear-gradient(160deg,#4f6b3d,#7b3aa0)" role="img" aria-label="Purple portable toilets on a trailer"></div><h3>Family reunions</h3></div>
  <div class="event-card is-active" style="left:443px;top:1024px"><div class="photo" style="background:linear-gradient(160deg,#3a5a34,#2a9a7c)" role="img" aria-label="Green portable toilets on a towed trailer"></div><h3>Team Building</h3></div>
  <div class="event-card" style="left:779px;top:1024px"><div class="photo" style="background:linear-gradient(160deg,#9aa6b0,#3c463a)" role="img" aria-label="Small restroom trailer by a waterfront"></div><h3>Wine Tastings</h3></div>

  <section class="products">
    <h2 class="section-title" style="top:78px">Our Product</h2>
    <div class="product-card" style="left:112px;top:155px"><div class="photo" style="background:linear-gradient(90deg,#d84aa8,#2f6bd0)" role="img" aria-label="Pink and blue portable toilets"></div><h3>Product Title</h3><div class="rule"></div><p>Lorem ipsum dolor sit amet, consectetur adipiscing elit, sed do eiusmod tempor</p><div class="more">LEARN MORE »</div></div>
    <div class="product-card" style="left:612px;top:155px"><div class="photo" style="background:linear-gradient(90deg,#c7ad86,#a8906a)" role="img" aria-label="Beige portable toilet"></div><h3>Product Title</h3><div class="rule"></div><p>Lorem ipsum dolor sit amet, consectetur adipiscing elit, sed do eiusmod tempor</p><div class="more">LEARN MORE »</div></div>
    <div class="product-card is-dark" style="left:112px;top:416px"><div class="photo" style="background:linear-gradient(90deg,#35b5ad,#2a9a93)" role="img" aria-label="Teal portable toilet"></div><h3>Product Title</h3><div class="rule"></div><p>Lorem ipsum dolor sit amet, consectetur adipiscing elit, sed do eiusmod tempor</p><div class="more">LEARN MORE »</div></div>
    <div class="product-card" style="left:612px;top:416px"><div class="photo" style="background:linear-gradient(90deg,#2a62d0,#7f8690)" role="img" aria-label="Blue and grey portable toilet"></div><h3>Product Title</h3><div class="rule"></div><p>Lorem ipsum dolor sit amet, consectetur adipiscing elit, sed do eiusmod tempor</p><div class="more">LEARN MORE »</div></div>
  </section>

  <section class="contact" role="img" aria-label="Faded photo of a crowd at an outdoor festival">
    <h2>Contact Us</h2>
    <p>Lorem ipsum dolor sit amet, consectetur adipiscing elit, sed do eiusmod tempor incididunt ut labore et dolore magna aliqua. Ut enim ad minim veniam, quis nostrud exercitation ullamco laboris nisi ut aliquip ex ea commodo consequat.</p>
  </section>
  <div class="contact-band"></div>

  <form class="quote">
    <h3>Request a Quote</h3>
    <div class="field" style="left:67px;top:123px">First Name<svg viewBox="0 0 14 14"><circle cx="7" cy="4" r="3.5"/><path d="M1 14c0-4 2.5-6 6-6s6 2 6 6z"/></svg></div>
    <div class="field" style="left:410px;top:123px">Type of event<svg viewBox="0 0 14 14"><circle cx="7" cy="4" r="3.5"/><path d="M1 14c0-4 2.5-6 6-6s6 2 6 6z"/></svg></div>
    <div class="field" style="left:67px;top:184px">Email Address<svg viewBox="0 0 14 14"><path d="M0 3h14v1.5L7 8.5 0 4.5z"/><path d="M0 6l7 4 7-4v6H0z"/></svg></div>
    <div class="field" style="left:410px;top:184px">Phone no<svg viewBox="0 0 14 14"><path d="M3 1l2.5 3-1.5 1.5c.8 1.8 2.2 3.2 4 4l1.5-1.5 3 2.5-1.5 2.5C6 13 1 8 .5 2.5z"/></svg></div>
    <div class="field" style="left:67px;top:245px">How many People ?<svg viewBox="0 0 14 14"><circle cx="7" cy="4" r="3.5"/><path d="M1 14c0-4 2.5-6 6-6s6 2 6 6z"/></svg></div>
    <div class="field" style="left:410px;top:245px">Type of Product You are interested in ?<svg viewBox="0 0 14 14"><circle cx="7" cy="4" r="3.5"/><path d="M1 14c0-4 2.5-6 6-6s6 2 6 6z"/></svg></div>
    <div class="field" style="left:67px;top:306px">When do you need it ?<svg viewBox="0 0 14 14"><path d="M0 3h14v1.5L7 8.5 0 4.5z"/><path d="M0 6l7 4 7-4v6H0z"/></svg></div>
    <div class="field" style="left:410px;top:306px">For How long ?<svg viewBox="0 0 14 14"><path d="M3 1l2.5 3-1.5 1.5c.8 1.8 2.2 3.2 4 4l1.5-1.5 3 2.5-1.5 2.5C6 13 1 8 .5 2.5z"/></svg></div>
    <div class="btn-submit">Submit Now</div>
  </form>

  <footer class="footer">
    <h4 style="left:112px;top:2883px">About Us</h4>
    <p class="about">Sed ut perspiciatis unde omnis iste natus error sit voluptatem accusant doloremque laudantium, totam rem</p>
    <h4 style="left:112px;top:3018px">Connect With Us</h4>
    <div class="social"><span></span><span></span><span></span><span></span></div>

    <h4 style="left:453px;top:2883px">Quick Links</h4>
    <ul style="left:453px;top:2922px"><li>Home</li><li>About Us</li><li>Our Events</li><li>Our Product</li><li>Contact Us</li></ul>

    <h4 style="left:673px;top:2883px">Our Events</h4>
    <ul style="left:673px;top:2922px"><li>Weddings</li><li>Private Parties</li><li>Festivals</li><li>Family Reunion</li><li>Wine Tasting</li></ul>

    <h4 style="left:925px;top:2883px">Other Links</h4>
    <ul style="left:925px;top:2922px"><li>FAQ</li><li>Terms Of Use</li><li>Privacy Policy</li><li>Help Service</li><li>News</li></ul>

    <div class="bottom-bar">© 2022 Tidewell Comforts. All Rights Reserved</div>
  </footer>

</div>
</body>
</html>
```